Etiketten-Design für Gin
Zielgruppe
Destillieren von GIN (BrunoLIK) / Zielgruppe alle die GIN Lieben :)
Aufgabenstellung
die Grunddatei besteht schon im AI Format, allerdings möchten wir gerne die Highlights in Kupfer haben wie Schrift und Holzfässer, gerne auch eigene Bilder entwerfen. Lediglich das BrunoLIK Logo (Kopf) sollte erhalten bleiben. Bitte die Datei so anlegen das die Highlights in Kupfer gedruckt (Siebdruck) werden können. Transparentes Etikett wäre super! Bei Fragen einfach melden :)

```html
<!DOCTYPE html>
<html lang="de">
<head>
<meta charset="utf-8">
<title>BrunoLIK Barrel Aged Gin – Etikett</title>
<link rel="stylesheet" href="https://fonts.googleapis.com/css2?family=Libre+Baskerville:ital,wght@0,400;0,700;1,400&display=swap">
<style>
  :root {
    --page: #eef0f1;
    --label-light: #e7e9ea;
    --label-mid: #b9bbbe;
    --label-dark: #7d7f83;
    --ink: #4f5156;
    --brand-grey: #6c6e73;
    --copper: #d98457;
    --copper-light: #eab393;
    --white: #ffffff;
  }
  html, body {
    margin: 0;
    width: 1197px;
    height: 1200px;
    overflow: hidden;
    background: var(--page);
  }
  .label {
    position: absolute;
    left: 98px;
    top: 130px;
    width: 1000px;
    height: 940px;
    overflow: hidden;
    font-family: "Libre Baskerville", Georgia, serif;
    color: var(--ink);
    text-align: center;
  }
  .label__texture {
    position: absolute;
    inset: 0;
    background:
      linear-gradient(90deg, var(--label-dark) 0%, var(--label-mid) 14%, var(--label-light) 32%, var(--label-light) 68%, var(--label-mid) 86%, var(--label-dark) 100%);
  }
  .label__content {
    position: relative;
    padding-top: 250px;
  }
  .brand {
    margin: 0;
    font-size: 92px;
    font-weight: 400;
    line-height: 1;
    color: var(--brand-grey);
  }
  .variety {
    margin: 14px 0 0;
    font-size: 34px;
    font-style: italic;
    color: var(--copper);
  }
  .description {
    margin: 46px auto 0;
    width: 860px;
    font-size: 25px;
    font-weight: 700;
    line-height: 1.42;
  }
  .web {
    margin: 34px 0 0;
    font-size: 24px;
    font-style: italic;
  }
  .address {
    margin: 12px 0 0;
    font-size: 27px;
    font-style: italic;
  }
  .label__footer {
    position: absolute;
    left: 0;
    right: 0;
    bottom: 50px;
    height: 110px;
  }
  .seal {
    position: absolute;
    left: 478px;
    top: 20px;
    width: 44px;
    height: 70px;
    border-radius: 10px;
    background: var(--copper-light);
  }
  .lot-field {
    position: absolute;
    right: 20px;
    top: 10px;
    width: 290px;
    height: 105px;
    background: var(--white);
  }
</style>
</head>
<body>
  <section class="label">
    <div class="label__texture" role="img" aria-label="Grau gewischte, verwitterte Holzstruktur als Etiketthintergrund"></div>
    <div class="label__content">
      <h1 class="brand">BrunoLIK</h1>
      <p class="variety">Barrel Aged Gin</p>
      <p class="description">
        Unser BrunoLIK „barrel aged GIN“<br>
        besteht aus unserem Schwäbischen Dry GIN,<br>
        dieser wird über 9 Monate nach Destillation in<br>
        einem Maulbeerbaumfass gelagert und gereift.<br>
        Dies rundet den Geschmack rauchig und kräftig ab
      </p>
      <p class="web">www.brunolik.de</p>
      <p class="address">Jonas Feld / Lindenweg 4 / 70173 Talheim</p>
    </div>
    <div class="label__footer">
      <div class="seal" aria-hidden="true"></div>
      <div class="lot-field" aria-hidden="true"></div>
    </div>
  </section>
</body>
</html>
```